Business card design needed

I run a Beautician studio (for 7 years now)
I offer
- Velmo Body Sugaring
- Ruby Glaze
- Nails
- Facials
- Manicure
- Foot Treatment
It might not be necessary to list all those treatments?
Maybe the link to the Website is sufficient?
I leave that up to you ...
(more info on www.FernAndDewByLenka.com.au)
Velmo BodySugaring is our biggest success, It replaces waxing.
I would like to incorporate the logo into the Business Card.
We had many complaints regarding our old Business Cards as the Phone Number was to small.
On the backside, we would like a "your next Appointment" section.
Looking forward to you Design, cheers ... Lenka
Industry/Entity Type
Business
Contact Information for Business Card
Fern by Dew by Lenka
14 Korrin Sqr 3942 Dunmore
www.FernAndDewByLenka.com.au
03 9481 2267

```html
<!DOCTYPE html>
<html lang="en">
<head>
<meta charset="utf-8">
<title>Velmo Body Sugaring – Business Cards</title>
<link href="https://fonts.googleapis.com/css2?family=Arimo:wght@400;700&family=Open+Sans:wght@400;600;700&family=Marcellus&display=swap" rel="stylesheet">
<style>
  :root {
    --backdrop: #1c1c1c;
    --card: #ffffff;
    --ink: #1a1a1a;
    --grey: #555555;
    --green: #1f9a3c;
    --leaf: #7cc242;
    --orange: #ec6a24;
    --line: #9a9a9a;
  }
  * { box-sizing: border-box; margin: 0; padding: 0; }
  html, body { width: 1200px; height: 719px; overflow: hidden; }
  body { background: var(--backdrop); position: relative; font-family: "Open Sans", Arial, sans-serif; color: var(--ink); }

  .card { position: absolute; background: var(--card); border-radius: 20px; overflow: hidden; }
  .card--front { left: 51px; top: 39px; width: 524px; height: 301px; }
  .card--appt-a { left: 606px; top: 39px; width: 525px; height: 300px; }
  .card--back { left: 53px; top: 372px; width: 524px; height: 298px; }
  .card--appt-b { left: 615px; top: 375px; width: 525px; height: 298px; }

  /* brand name */
  .brand { position: absolute; text-align: center; font-family: "Marcellus", serif; color: var(--ink); }
  .brand__dot { display: block; margin: 0 auto 10px; border-radius: 50%; background: var(--orange); }
  .brand__name { display: block; line-height: 1.05; }

  .card--front .brand { left: 28px; top: 66px; width: 230px; }
  .card--front .brand__dot { width: 52px; height: 52px; }
  .card--front .brand__name { font-size: 30px; }

  .divider { position: absolute; left: 255px; top: 30px; width: 1px; height: 200px; background: #cccccc; }

  .contact { position: absolute; left: 268px; top: 32px; font-family: "Arimo", Arial, sans-serif; }
  .contact__row { display: flex; align-items: center; gap: 8px; font-size: 16px; height: 26px; }
  .contact__row--phone { font-size: 17px; }
  .contact__row--web { font-size: 14px; }
  .contact__icon { width: 14px; height: 14px; flex: none; }
  .treatments { margin-top: 12px; }
  .treatments__title { font-family: "Open Sans", sans-serif; font-weight: 700; color: var(--green); font-size: 16px; letter-spacing: 0.5px; margin-bottom: 2px; }
  .treatments__list { list-style: none; font-size: 14px; line-height: 21px; }

  .footer-band { position: absolute; left: 0; bottom: 0; width: 100%; height: 50px; background: var(--orange); border-top: 4px solid var(--leaf); }
  .studio { position: absolute; left: 10px; bottom: 8px; color: #fff; font-family: "Arimo", Arial, sans-serif; }
  .studio__name { font-weight: 700; font-size: 15px; }
  .studio__address { font-size: 13px; margin-top: 1px; }

  /* back */
  .card--back .brand { left: 0; width: 100%; top: 20px; }
  .card--back .brand__dot { width: 62px; height: 62px; }
  .card--back .brand__name { font-size: 32px; }
  .back__web { position: absolute; left: 0; width: 100%; top: 201px; text-align: center; font-family: "Arimo", Arial, sans-serif; font-size: 14px; letter-spacing: 2.4px; }
  .hours { position: absolute; left: 0; width: 100%; top: 232px; text-align: center; color: var(--grey); font-weight: 700; }
  .hours__title { font-size: 20px; letter-spacing: 1px; }
  .hours__times { font-size: 15px; margin-top: 6px; }
  .hours__sep { color: #bbbbbb; font-weight: 400; margin: 0 8px; }

  /* appointment cards */
  .appt { position: absolute; left: 0; top: 0; width: 100%; height: 100%; color: #333; font-size: 15px; }
  .card--appt-b .appt { left: 10px; top: 4px; }
  .appt__title { position: absolute; left: 36px; top: 54px; font-family: "Marcellus", serif; color: var(--green); font-size: 17px; letter-spacing: 0.5px; }
  .appt__label { position: absolute; }
  .appt__rule { position: absolute; border-bottom: 1px dotted var(--line); height: 1px; }
  .appt__rule--solid { border-bottom: 1px solid var(--line); }
  .appt__box { position: absolute; border: 1px solid #777; width: 32px; height: 20px; }
  .appt__box--wide { width: 95px; }
  .appt__day { position: absolute; top: 204px; font-weight: 600; color: #555; font-size: 14px; }
  .appt__note { position: absolute; left: 32px; top: 250px; width: 470px; font-size: 12.5px; line-height: 17px; }

  .card--appt-b .brand { right: 56px; top: 12px; width: 110px; }
  .card--appt-b .brand__dot { width: 26px; height: 26px; margin-bottom: 4px; }
  .card--appt-b .brand__name { font-size: 13px; }
  .card--appt-b .appt__title { top: 50px; }
</style>
</head>
<body>

  <!-- Front -->
  <section class="card card--front">
    <div class="brand">
      <span class="brand__dot"></span>
      <span class="brand__name">Velmo<br>Body Sugaring</span>
    </div>
    <div class="divider"></div>
    <div class="contact">
      <div class="contact__row contact__row--phone">
        <svg class="contact__icon" viewBox="0 0 24 24"><path fill="#1a1a1a" d="M6.6 10.8a15.1 15.1 0 0 0 6.6 6.6l2.2-2.2a1 1 0 0 1 1-.25 11.4 11.4 0 0 0 3.6.57 1 1 0 0 1 1 1V20a1 1 0 0 1-1 1A17 17 0 0 1 3 4a1 1 0 0 1 1-1h3.5a1 1 0 0 1 1 1c0 1.25.2 2.45.57 3.57a1 1 0 0 1-.25 1z"/></svg>
        <span>03 9481 2267</span>
      </div>
      <div class="contact__row contact__row--web">
        <svg class="contact__icon" viewBox="0 0 24 24" fill="none" stroke="#2e8b3a" stroke-width="2"><circle cx="12" cy="12" r="10"/><path d="M2 12h20M12 2a15 15 0 0 1 0 20M12 2a15 15 0 0 0 0 20"/></svg>
        <span>www.FernAndDewByLenka.com.au</span>
      </div>
      <div class="treatments">
        <h2 class="treatments__title">Treatments offer</h2>
        <ul class="treatments__list">
          <li>• Velmo Body Sugaring</li>
          <li>• Ruby Glaze • Nails</li>
          <li>• Facials • Manicure</li>
          <li>• Foot Treatment</li>
        </ul>
      </div>
    </div>
    <div class="footer-band"></div>
    <div class="studio">
      <div class="studio__name">Fern by Dew by Lenka</div>
      <div class="studio__address">14 Korrin Sqr 3942 Dunmore</div>
    </div>
  </section>

  <!-- Appointment A -->
  <section class="card card--appt-a">
    <div class="appt">
      <h2 class="appt__title">YOUR APPOINTMENT</h2>
      <span class="appt__label" style="left:35px;top:90px">Name :</span>
      <span class="appt__rule" style="left:95px;top:105px;width:292px"></span>
      <span class="appt__label" style="left:35px;top:128px">Date :</span>
      <span class="appt__rule appt__rule--solid" style="left:96px;top:143px;width:94px"></span>
      <span class="appt__label" style="left:196px;top:128px">Time :</span>
      <span class="appt__rule appt__rule--solid" style="left:242px;top:143px;width:88px"></span>
      <span class="appt__label" style="left:334px;top:128px">am / pm</span>
      <span class="appt__label" style="left:35px;top:166px">Next Appointment</span>
      <span class="appt__box appt__box--wide" style="left:178px;top:165px"></span>
      <span class="appt__box appt__box--wide" style="left:306px;top:165px"></span>
      <span class="appt__day" style="left:32px">MON</span><span class="appt__box" style="left:77px;top:204px"></span>
      <span class="appt__day" style="left:117px">TUE</span><span class="appt__box" style="left:153px;top:204px"></span>
      <span class="appt__day" style="left:193px">WED</span><span class="appt__box" style="left:236px;top:204px"></span>
      <span class="appt__day" style="left:275px">THU</span><span class="appt__box" style="left:315px;top:204px"></span>
      <span class="appt__day" style="left:355px">FRI</span><span class="appt__box" style="left:385px;top:204px"></span>
      <span class="appt__day" style="left:425px">SAT</span><span class="appt__box" style="left:460px;top:204px"></span>
      <p class="appt__note">It would be appreciated if 24 hours notice could be given if you are unable to attend an appointment</p>
    </div>
  </section>

  <!-- Back -->
  <section class="card card--back">
    <div class="brand">
      <span class="brand__dot"></span>
      <span class="brand__name">Velmo<br>Body Sugaring</span>
    </div>
    <div class="back__web">www.FernAndDewByLenka.com.au</div>
    <div class="hours">
      <h2 class="hours__title">Hours of Operation</h2>
      <p class="hours__times">Mon - Fri: 8.00am - 6.30pm<span class="hours__sep">|</span>Saturday: 8.00am - 1.00pm</p>
    </div>
  </section>

  <!-- Appointment B -->
  <section class="card card--appt-b">
    <div class="brand">
      <span class="brand__dot"></span>
      <span class="brand__name">Velmo<br>Body Sugaring</span>
    </div>
    <div class="appt">
      <h2 class="appt__title">YOUR APPOINTMENT</h2>
      <span class="appt__label" style="left:25px;top:84px">Name :</span>
      <span class="appt__rule" style="left:85px;top:99px;width:292px"></span>
      <span class="appt__label" style="left:25px;top:122px">Date :</span>
      <span class="appt__rule appt__rule--solid" style="left:86px;top:137px;width:94px"></span>
      <span class="appt__label" style="left:186px;top:122px">Time :</span>
      <span class="appt__rule appt__rule--solid" style="left:232px;top:137px;width:88px"></span>
      <span class="appt__label" style="left:324px;top:122px">am / pm</span>
      <span class="appt__label" style="left:25px;top:160px">Next Appointment</span>
      <span class="appt__box appt__box--wide" style="left:168px;top:159px"></span>
      <span class="appt__box appt__box--wide" style="left:296px;top:159px"></span>
      <span class="appt__day" style="left:22px;top:198px">MON</span><span class="appt__box" style="left:67px;top:198px"></span>
      <span class="appt__day" style="left:107px;top:198px">TUE</span><span class="appt__box" style="left:143px;top:198px"></span>
      <span class="appt__day" style="left:183px;top:198px">WED</span><span class="appt__box" style="left:226px;top:198px"></span>
      <span class="appt__day" style="left:265px;top:198px">THU</span><span class="appt__box" style="left:305px;top:198px"></span>
      <span class="appt__day" style="left:345px;top:198px">FRI</span><span class="appt__box" style="left:375px;top:198px"></span>
      <span class="appt__day" style="left:415px;top:198px">SAT</span><span class="appt__box" style="left:450px;top:198px"></span>
      <p class="appt__note" style="left:22px;top:244px">It would be appreciated if 24 hours notice could be given if you are unable to attend an appointment</p>
    </div>
  </section>

</body>
</html>
```